Venture Capital Investment Firm

We are looking to overhaul our existing website (substantially), with only using the same logos (which we can provide).
We are an investment firm that focuses on making loans to late stage technology companies. Our site should ultimately look like other venture capital firms, and look modern and fresh. We have an existing website www.norvellhub.com which this will be replacing, although we will be using a lot of the existing written content, and potentially the numbers of pages we will need, we are not wed to anything else. Please feel free to shoot any questions at any time and thank you in advance for your help!
Websites we like as examples:
https://www.tesmarkfund.com/
https://www.brindlewoodpartners.com/
Target Market(s)
Potential investors who will invest in our firm, as well as potentially companies that are looking to borrow money from us.
Coding
Coded - Design and coding required
Number of Pages Required
5+ page
Colors
Designer to choose colors to be used in the design.
Look and feel

```html
<!DOCTYPE html>
<html lang="en">
<head>
<meta charset="utf-8">
<title>Arbor Ledger — Structured Credit Investment</title>
<link rel="stylesheet" href="https://fonts.googleapis.com/css2?family=Cinzel:wght@400;600;700&family=Mulish:wght@300;400;600;700&display=swap">
<style>
:root{
  --navy:#0b0a33;
  --navy-deep:#08072a;
  --violet:#4a3f8f;
  --accent:#2f9fe0;
  --ink:#1a1a2e;
  --muted:#6b6b78;
  --rule:#d9d9de;
  --mist:#efefef;
  --white:#ffffff;
}
*{box-sizing:border-box;margin:0;padding:0}
html,body{width:1200px;height:4222px;overflow:hidden}
body{position:relative;background:var(--white);font-family:'Mulish',sans-serif;color:var(--ink)}
.abs{position:absolute}
.serif{font-family:'Cinzel',serif}

/* header */
.site-header{left:0;top:0;width:1200px;height:98px;background:var(--navy);z-index:3}
.brand{display:flex;align-items:center;gap:14px;color:var(--white);font-family:'Cinzel',serif;font-weight:400;font-size:34px;letter-spacing:1px}
.brand-dot{width:40px;height:40px;border:3px solid var(--white);border-radius:50%}
.site-header .brand{position:absolute;left:144px;top:22px}
.header-mail{right:144px;top:20px;color:var(--white);font-size:15px;display:flex;align-items:center;gap:10px}
.main-nav{right:144px;top:64px;display:flex;gap:36px}
.main-nav a{color:var(--white);text-decoration:none;font-family:'Cinzel',serif;font-size:12.5px;letter-spacing:.5px;position:relative}
.main-nav a.is-active::after{content:"";position:absolute;left:0;right:0;bottom:-8px;height:3px;background:var(--accent)}

/* hero */
.hero{left:0;top:98px;width:1200px;height:628px;background:linear-gradient(180deg,#3d4560 0%,#4f4a66 45%,#6a4a60 75%,#2a2c48 100%)}
.hero-title{left:0;top:336px;width:1200px;text-align:center;color:var(--white);font-family:'Cinzel',serif;font-size:40px;line-height:48px;letter-spacing:1px}
.hero-dots{left:546px;top:620px;display:flex;gap:6px}
.hero-dots span{width:42px;height:4px;background:var(--white)}
.hero-dots span.off{background:transparent;border:1px solid var(--white)}
.hero-cut{left:0;top:680px}

/* section headings */
.section-title{width:1200px;left:0;text-align:center;font-family:'Cinzel',serif;font-weight:600;font-size:38px;color:var(--navy);letter-spacing:1px}

/* welcome */
.welcome-lead{left:0;top:888px;width:1200px;text-align:center;font-size:18px;line-height:30px;color:var(--muted);font-weight:300}
.focus-col{width:287px;text-align:center}
.focus-col svg{display:block;margin:0 auto}
.focus-col h3{margin-top:18px;font-size:18px;font-weight:400;color:var(--ink);letter-spacing:.5px}
.focus-col p{margin-top:18px;font-size:13px;line-height:25.5px;color:var(--muted)}
.btn-outline{border:2px solid var(--navy);border-radius:30px;font-weight:700;font-size:14px;color:var(--navy);display:flex;align-items:center;justify-content:center;letter-spacing:.5px}
.divider{left:144px;top:1427px;width:912px;height:1px;background:var(--rule)}

/* about */
.about-title{left:144px;top:1508px;font-family:'Cinzel',serif;font-weight:600;font-size:38px;color:var(--navy)}
.about-text{left:144px;top:1576px;width:518px;font-size:13px;line-height:28px;color:var(--muted)}
.about-visual{left:728px;top:1514px;width:328px;height:380px;border-radius:164px 164px 164px 164px/190px 190px 190px 190px;background:linear-gradient(135deg,#c9cfd8,#e8ecf1 50%,#8da2c4)}

/* team */
.team{left:0;top:1978px;width:1200px;height:565px;background:linear-gradient(160deg,#14124a,var(--navy-deep))}
.team .section-title{color:var(--white);top:66px}
.member{width:320px;text-align:center;color:var(--white)}
.member-photo{width:268px;height:268px;margin:0 auto;border-radius:50%;border:3px solid var(--violet);padding:8px}
.member-photo div{width:100%;height:100%;border-radius:50%;background:radial-gradient(circle at 50% 40%,#6c6c70,#1d1d22 75%)}
.member-photo.is-hover div{background:#4e4a9a;display:flex;align-items:center;justify-content:center}
.member h4{margin-top:22px;font-size:22px;font-weight:400}
.member p{margin-top:8px;font-size:13px}

/* why */
.why{left:0;top:2543px;width:1200px;height:504px;background:var(--mist)}
.why .section-title{top:58px;color:var(--ink)}
.reason{width:260px}
.reason h4{font-size:19px;font-weight:400;color:#333}
.reason p{margin-top:8px;font-size:11.5px;line-height:18px;color:#555}
.reason-icon{}

/* news */
.news-title{top:3128px}
.news-feature{left:143px;top:3227px;width:913px;height:325px;background:var(--white);box-shadow:0 2px 14px rgba(0,0,0,.16);border-radius:4px;overflow:hidden}
.news-feature .photo{position:absolute;left:0;top:0;width:451px;height:325px;background:linear-gradient(135deg,#d9dde3,#f2f3f5 45%,#7f97bf)}
.news-feature .copy{position:absolute;left:483px;top:44px;width:400px}
.news-date{font-size:15px;color:#555;display:flex;align-items:center;gap:4px}
.news-feature h3{margin-top:18px;font-size:21px;line-height:30px;font-weight:600;color:var(--navy)}
.news-feature p{margin-top:16px;font-size:12.5px;line-height:25px;color:#666;text-align:justify}
.news-card{width:219px}
.news-card .photo{height:167px;border-radius:8px}
.news-card .news-date{margin-top:14px}
.news-card h4{margin-top:12px;font-size:16.5px;line-height:21px;font-weight:400;color:var(--navy)}

/* footer */
.site-footer{left:0;top:3940px;width:1200px;height:282px}
.footer-brand{left:0;top:4012px;width:1200px;display:flex;justify-content:center}
.copyright{left:0;top:4104px;width:1200px;text-align:center;color:var(--white);font-size:12px}
.copyright u{text-decoration:underline}
.social{left:526px;top:4148px;display:flex;gap:6px}
.social span{width:32px;height:32px;border-radius:50%;background:var(--white)}
</style>
</head>
<body>

<header class="site-header abs">
  <div class="brand"><span class="brand-dot"></span>Arbor Ledger</div>
  <div class="header-mail abs">
    <svg width="16" height="12" viewBox="0 0 16 12"><rect width="16" height="12" rx="1" fill="#fff"/><path d="M1 1l7 5 7-5" stroke="#0b0a33" stroke-width="1.4" fill="none"/></svg>
    Email: inquiries@arborledger.com
  </div>
  <nav class="main-nav abs">
    <a class="is-active" href="#">HOME</a><a href="#">STRATEGY</a><a href="#">ABOUT US</a><a href="#">TEAM</a><a href="#">NEWS</a><a href="#">CONTACT</a><a href="#">INVESTORS</a>
  </nav>
</header>

<section class="hero abs" role="img" aria-label="Silhouettes of business people over a city skyline and world map"></section>
<h1 class="hero-title abs">WE ARE A GLOBAL STRUCTURED<br>CREDIT INVESTMENT FIRM</h1>
<div class="hero-dots abs"><span></span><span></span><span class="off"></span><span></span></div>
<svg class="hero-cut abs" width="1200" height="50" viewBox="0 0 1200 50"><polygon points="0,46 1200,14 1200,50 0,50" fill="#fff"/><polygon points="760,34 1200,8 1200,14 0,46 0,46" fill="#0b0a33"/></svg>

<h2 class="section-title abs" style="top:812px">Welcome to Arbor Ledger</h2>
<p class="welcome-lead abs">WE ARE A GLOBAL STRUCTURED CREDIT INVESTMENT FIRM FOCUSED<br>ON THE HEALTHCARE AND TECHNOLOGY INDUSTRIES</p>

<div class="focus-col abs" style="left:134px;top:1010px">
  <svg width="60" height="70" viewBox="0 0 60 70" fill="none" stroke="#1a1a2e" stroke-width="2"><path d="M30 4a20 20 0 0 0-12 36v10h24V40A20 20 0 0 0 30 4z"/><path d="M22 56h16M24 62h12"/><circle cx="30" cy="24" r="7"/></svg>
  <h3>INDUSTRY</h3>
  <p>Our focus spans the life science and technology industries, two sectors where intellectual property (IP) is an integral driver of asset and enterprise value.</p>
</div>
<div class="focus-col abs" style="left:456px;top:1010px">
  <svg width="60" height="70" viewBox="0 0 60 70" fill="none" stroke="#1a1a2e" stroke-width="2"><path d="M6 60V46h8v14M18 60V38h8v22M30 60V30h8v30"/><path d="M6 34l16-12 10 6 18-18M42 10h8v8"/><circle cx="48" cy="54" r="8"/></svg>
  <h3>LIFE SCIENCES</h3>
  <p>We have a long track record of partnering with companies and investors that create and commercialize life science products, We have a long track record</p>
</div>
<div class="focus-col abs" style="left:774px;top:1010px">
  <svg width="70" height="70" viewBox="0 0 70 70" fill="none" stroke="#1a1a2e" stroke-width="2"><rect x="8" y="16" width="54" height="34" rx="2"/><path d="M2 56h66l-4 5H6z"/><path d="M20 42V34M30 42V28M40 42V32M48 42V26"/><circle cx="60" cy="12" r="5"/></svg>
  <h3>TECHNOLOGY</h3>
  <p>We uniquely offer sizeable and flexible structured credit financing solutions to innovative technology companies, with a focus on enterprise software</p>
</div>
<div class="btn-outline abs" style="left:434px;top:1307px;width:332px;height:46px">LEARN MORE ABOUT OUR STRATEGY</div>
<div class="divider abs"></div>

<h2 class="about-title abs">About Us</h2>
<p class="about-text abs">Arbor Ledger is a private investment firm unique in its dual focus on life science and technology credit opportunities. Our ambidextrous approach to investing reflects a broad recognition and appreciation for the critical role intellectual property plays in the successful commercialization of products. We apply our extensive industry expertise to assess the revenue visibility created by these assets and offer a range of creative financing solutions. A pioneer in providing life science structured credit beginning in 2004, the Arbor Ledger team was the first to introduce flexible structured credit to the technology.</p>
<div class="btn-outline abs" style="left:144px;top:1825px;width:131px;height:45px">READ MORE</div>
<div class="about-visual abs" role="img" aria-label="Business people reviewing financial charts at a desk"></div>

<section class="team abs">
  <h2 class="section-title abs">Our Team</h2>
  <div class="member abs" style="left:122px;top:135px"><div class="member-photo"><div role="img" aria-label="Portrait of team member"></div></div><h4>Marcus Elwood</h4><p>Life Sciences, Technology</p></div>
  <div class="member abs" style="left:440px;top:135px"><div class="member-photo is-hover"><div role="img" aria-label="Portrait of team member"><span style="width:42px;height:42px;border:2px solid #fff;border-radius:50%;display:block"></span></div></div><h4>Daniel Farrow</h4><p>Technology</p></div>
  <div class="member abs" style="left:760px;top:135px"><div class="member-photo"><div role="img" aria-label="Portrait of team member"></div></div><h4>Owen Prescott</h4><p>Chief Operating Office</p></div>
</section>

<section class="why abs">
  <h2 class="section-title abs">Why Choose Us?</h2>
  <svg class="abs" style="left:144px;top:168px" width="72" height="72" viewBox="0 0 72 72" fill="none" stroke="#1a1a2e" stroke-width="2.4"><rect x="4" y="4" width="46" height="40"/><path d="M12 32l10-12 8 8 12-14"/><circle cx="48" cy="50" r="10"/><path d="M55 57l12 12"/></svg>
  <div class="reason abs" style="left:236px;top:168px"><h4>Consectetad</h4><p>Lorem ipsum dolloor sikit ameto nsectet orem ipsum dolloor sikit ametsectetacin eiusm adipcing elbnp eiusm</p></div>
  <svg class="abs" style="left:144px;top:304px" width="60" height="76" viewBox="0 0 60 76" fill="none" stroke="#1a1a2e" stroke-width="2.4"><path d="M4 8h52L36 34v12H24V34z"/><circle cx="30" cy="60" r="11"/><path d="M30 53v14M26 57h6a3 3 0 0 1 0 6h-5"/></svg>
  <div class="reason abs" style="left:236px;top:304px"><h4>Consectetad</h4><p>Lorem ipsum dolloor sikit ameto nsectet orem ipsum dolloor sikit ametsectetacin eiusm adipcing elbnp eiusm</p></div>
  <svg class="abs" style="left:738px;top:164px" width="66" height="76" viewBox="0 0 66 76" fill="none" stroke="#1a1a2e" stroke-width="2.4"><circle cx="33" cy="20" r="9"/><circle cx="33" cy="20" r="16" stroke-dasharray="6 4"/><circle cx="14" cy="50" r="6"/><circle cx="52" cy="50" r="6"/><circle cx="33" cy="48" r="6"/><path d="M4 72c0-10 20-10 20 0M23 72c0-10 20-10 20 0M42 72c0-10 20-10 20 0"/></svg>
  <div class="reason abs" style="left:817px;top:168px"><h4>Consectetad</h4><p>Lorem ipsum dolloor sikit ameto nsectet orem ipsum dolloor sikit ametsectetacin eiusm adipcing elbnp eiusm</p></div>
  <svg class="abs" style="left:738px;top:304px" width="70" height="70" viewBox="0 0 70 70" fill="none" stroke="#1a1a2e" stroke-width="2.4"><rect x="4" y="4" width="62" height="62" rx="10"/><circle cx="32" cy="32" r="16"/><circle cx="32" cy="32" r="7"/><path d="M34 34l18 18 4-8 6-2z" fill="#fff"/></svg>
  <div class="reason abs" style="left:817px;top:304px"><h4>Consectetad</h4><p>Lorem ipsum dolloor sikit ameto nsectet orem ipsum dolloor sikit ametsectetacin eiusm adipcing elbnp eiusm</p></div>
</section>

<h2 class="section-title news-title abs">ARBOR LEDGER NEWS</h2>
<article class="news-feature abs">
  <div class="photo" role="img" aria-label="Hand holding a pen over printed financial charts"></div>
  <div class="copy">
    <div class="news-date"><svg width="14" height="14" viewBox="0 0 14 14" fill="none" stroke="#555" stroke-width="1.4"><rect x="1" y="2" width="12" height="11"/><path d="M1 5h12M4 0v3M10 0v3"/></svg>April 2019</div>
    <h3>Arbor Ledger completes structured debt investment in Trellisoft</h3>
    <p>Arbor Ledger Investment Partners (“Arbor Ledger”) announced today that it has completed a structured debt investment in Trellisoft, Inc. (“Trellisoft”), the leader in employee communication. The financing will be used to advance Trellisoft’s continued growth as the SaaS</p>
  </div>
</article>

<div class="news-card abs" style="left:143px;top:3585px"><div class="photo" role="img" aria-label="Stock market data on screens" style="background:linear-gradient(160deg,#d8c7e6,#5a6fa8 55%,#1c2344)"></div><div class="news-date"><svg width="14" height="14" viewBox="0 0 14 14" fill="none" stroke="#555" stroke-width="1.4"><rect x="1" y="2" width="12" height="11"/><path d="M1 5h12M4 0v3M10 0v3"/></svg>April 2019</div><h4>Arbor Ledger completes structured credit</h4></div>
<div class="news-card abs" style="left:374px;top:3585px"><div class="photo" role="img" aria-label="Laptop with charts on a desk" style="background:linear-gradient(160deg,#3b4f74,#1e2a44 60%,#8a94a8)"></div><div class="news-date"><svg width="14" height="14" viewBox="0 0 14 14" fill="none" stroke="#555" stroke-width="1.4"><rect x="1" y="2" width="12" height="11"/><path d="M1 5h12M4 0v3M10 0v3"/></svg>April 2019</div><h4>Structured credit investment in Corvane</h4></div>
<div class="news-card abs" style="left:607px;top:3585px"><div class="photo" role="img" aria-label="Business meeting around a table" style="background:linear-gradient(160deg,#e9e4dc,#a79886 55%,#4b4a55)"></div><div class="news-date"><svg width="14" height="14" viewBox="0 0 14 14" fill="none" stroke="#555" stroke-width="1.4"><rect x="1" y="2" width="12" height="11"/><path d="M1 5h12M4 0v3M10 0v3"/></svg>April 2019</div><h4>Arbor Ledger completes structured credit</h4></div>
<div class="news-card abs" style="left:838px;top:3585px"><div class="photo" role="img" aria-label="Hands reviewing documents on a desk" style="background:linear-gradient(160deg,#f0e6cf,#c9c3b6 50%,#6f7d92)"></div><div class="news-date"><svg width="14" height="14" viewBox="0 0 14 14" fill="none" stroke="#555" stroke-width="1.4"><rect x="1" y="2" width="12" height="11"/><path d="M1 5h12M4 0v3M10 0v3"/></svg>April 2019</div><h4>Arbor Ledger completes structured credit</h4></div>

<svg class="site-footer abs" width="1200" height="282" viewBox="0 0 1200 282"><polygon points="0,37 1200,0 1200,282 0,282" fill="#0b0a33"/></svg>
<div class="footer-brand abs"><div class="brand"><span class="brand-dot"></span>Arbor Ledger</div></div>
<p class="copyright abs">© 2019 Arbor Ledger Investment Partners LLC.&nbsp; All Rights Reserved. <u>Legal Disclaimer</u></p>
<div class="social abs"><span></span><span></span><span></span><span></span></div>

</body>
</html>
```